Homemaking training schools needs a Business Card design

Designer, Hello!

No special requirements, good-looking enough.
--------------------------------------------------------------------------

Name: Marcus Dole
Chairman
Tel: 0574-71948263
Mobile: 13857420916
Email: kelvora@mailnest.example
Web: www.prt2019.example
Add: No.258, LanpingJie, BeiyuanQu, Ningbo, Zhejiang

LOGO
Ningbo PRT Homemaking Training School

Target Market(s)

pregnant women, mothers, infants, the elderly and families, including cleaning, cooking, nursing training.

Industry/Entity Type

Business

Contact Information for Business Card

Name: Marcus Dole
Chairman
Tel: 0574-71948263
Mobile: 13857420916
Email: kelvora@mailnest.example
Web: www.prt2019.example

LOGO

Font styles to use
Serif
Sans Serif
Decorative

Requirements
Nice to have
• Feels: clean, specifications, safety, comfort, warmth and happiness.

```html
<!DOCTYPE html>
<html lang="en">
<head>
<meta charset="utf-8">
<title>PeiRuiTang Business Card</title>
<link rel="stylesheet" href="https://fonts.googleapis.com/css2?family=Quicksand:wght@400;500;600&display=swap">
<style>
  :root{
    --bg:#3a3c40;
    --paper:#f1efed;
    --blue:#1f6fb2;
    --blue-bright:#1b8fd3;
    --magenta:#e0128c;
    --band:#dcdbd9;
    --ghost:#d6d5d3;
    --ink:#2e2e30;
    --muted:#6f6a66;
  }
  *{margin:0;padding:0;box-sizing:border-box}
  html,body{width:1200px;height:918px;overflow:hidden;background:var(--bg)}
  body{font-family:"Quicksand",sans-serif;color:var(--ink);position:relative}
  .card{position:absolute;left:300px;width:600px;height:360px;background:var(--paper);overflow:hidden;box-shadow:0 10px 30px rgba(0,0,0,.35)}
  .card--front{top:59px}
  .card--back{top:479px}

  /* front */
  .front-accent{position:absolute;inset:0}
  .brand{position:absolute;left:0;right:0;top:130px;text-align:center}
  .brand-line{display:inline-flex;align-items:center;gap:10px}
  .brand-name{font-size:44px;font-weight:600;color:var(--blue-bright);letter-spacing:.5px}
  .brand-dot{width:16px;height:16px;border-radius:50%;background:var(--magenta)}
  .brand-tagline{display:flex;align-items:center;justify-content:center;gap:10px;margin-top:6px;font-size:13px;color:var(--muted);letter-spacing:1px}
  .brand-tagline::before,.brand-tagline::after{content:"";width:70px;height:1px;background:#8a5a4a}

  /* back */
  .back-shapes{position:absolute;inset:0}
  .holder{position:absolute;left:34px;top:44px;color:#fff}
  .holder-name{font-size:32px;font-weight:500;line-height:1;letter-spacing:.5px}
  .holder-title{font-size:16px;font-weight:500;margin-top:4px;opacity:.9}
  .contacts{position:absolute;left:300px;top:150px;list-style:none;font-size:16px;font-weight:500}
  .contacts li{display:flex;align-items:flex-start;gap:14px;line-height:22px}
  .contacts .gap{margin-top:12px}
  .contacts svg{width:16px;height:16px;margin-top:3px;flex:none}
  .address{max-width:270px}
</style>
</head>
<body>

<section class="card card--front" aria-label="Card front">
  <svg class="front-accent" viewBox="0 0 600 360" aria-hidden="true">
    <polygon points="540,0 600,0 600,120" fill="var(--blue-bright)"/>
    <polygon points="0,250 0,360 90,360" fill="var(--magenta)"/>
  </svg>
  <div class="brand">
    <div class="brand-line">
      <span class="brand-name">PeiRuiTang</span>
      <span class="brand-dot"></span>
    </div>
    <div class="brand-tagline">Training &amp; Services</div>
  </div>
</section>

<section class="card card--back" aria-label="Card back">
  <svg class="back-shapes" viewBox="0 0 600 360" aria-hidden="true">
    <polygon points="270,82 600,82 600,140 240,140" fill="var(--band)"/>
    <polygon points="0,30 300,30 265,110 0,110" fill="var(--blue)"/>
    <circle cx="110" cy="260" r="70" fill="var(--ghost)" opacity=".7"/>
    <rect x="90" y="352" width="510" height="8" fill="var(--magenta)"/>
  </svg>

  <div class="holder">
    <div class="holder-name">Marcus Dole</div>
    <div class="holder-title">Chairman</div>
  </div>

  <ul class="contacts">
    <li>
      <svg viewBox="0 0 16 16" aria-hidden="true"><rect x="1" y="1" width="14" height="14" rx="3" fill="var(--ink)"/><path d="M5 4.5c0 4 2.5 6.5 6.5 6.5l.5-1.8-2-.8-.8.8c-1.2-.6-2-1.4-2.6-2.6l.8-.8-.8-2z" fill="#fff"/></svg>
      <span>0574-71948263</span>
    </li>
    <li>
      <svg viewBox="0 0 16 16" aria-hidden="true"><rect x="1" y="1" width="14" height="14" rx="3" fill="var(--ink)"/><path d="M5 4.5c0 4 2.5 6.5 6.5 6.5l.5-1.8-2-.8-.8.8c-1.2-.6-2-1.4-2.6-2.6l.8-.8-.8-2z" fill="#fff"/></svg>
      <span>138 574 209 16</span>
    </li>
    <li class="gap">
      <svg viewBox="0 0 16 16" aria-hidden="true"><rect x="1" y="3" width="14" height="10" fill="none" stroke="var(--ink)" stroke-width="1.4"/><path d="M1 3l7 6 7-6" fill="none" stroke="var(--ink)" stroke-width="1.4"/></svg>
      <span>kelvora@mailnest.example</span>
    </li>
    <li>
      <svg viewBox="0 0 16 16" aria-hidden="true"><g fill="none" stroke="var(--ink)" stroke-width="1.3"><circle cx="8" cy="8" r="6.5"/><ellipse cx="8" cy="8" rx="3" ry="6.5"/><path d="M1.5 8h13"/></g></svg>
      <span>www.prt2019.example</span>
    </li>
    <li class="gap">
      <svg viewBox="0 0 16 16" aria-hidden="true"><path d="M8 1a5 5 0 0 0-5 5c0 4 5 9 5 9s5-5 5-9a5 5 0 0 0-5-5z" fill="var(--ink)"/><circle cx="8" cy="6" r="1.8" fill="#fff"/></svg>
      <span class="address">No.258, LanpingJie, BeiyuanQu, Ningbo, Zhejiang</span>
    </li>
  </ul>
</section>

</body>
</html>
```